develop our online residential property development appraisal service

This project requires a detailed WordPress design to represent a new digital residential property development consultancy business. At its heart it will have a number of different products that essentially advise customers of the potential value and feasibility of developing their residential site into multiple townhouses, units, apartments, etc... This will be accompanied by explaining the considerations of residential property development.

We aim to navigate and break down this complex area and provide our customers with the tools, knowledge, control and power to 'unlock the value' in their property.

REFERENCE DOCUMENTS:
1. Detailed solution requirements please refer to the attached 'wordpressdesignrequirements'
2. Logo files, style guide and colour pallet please refer to the attached 'KRLM.zip'
3. Site Map refer to attached 'wordpressdesignsitemap'

Reason: Additional information provided so extending period for designs to take into account.

Target Market(s)

The site will appeal to professional service providers; accountants, financial planners, lawyers, etc…

Industry/Entity Type

Residential

Font styles to use
Sans Serif
Other font styles liked:
• Similar to the logo font, slim line and simple

Requirements
Must have
• The logo, style and colour palette provided in the attached 'KRLM.zip' files
• Satisfy the intent of the 'wordpressdesignrequirements'
• Present as an online-centric business
• Clean, crisp and modern design
• Predominant use of white as a background contrasted with the colours provided in the colour palette
Nice to have
• Use of the following WordPress business themes is encouraged but not mandatory:
• 1. Mavo
• 2. Tulek
• 3. Vupa
Should not have
• Overt references to Australia

```html
<!DOCTYPE html>
<html lang="en">
<head>
<meta charset="utf-8">
<title>KRLM – Mavo</title>
<link rel="stylesheet" href="https://fonts.googleapis.com/css2?family=PT+Sans:wght@400;700&family=Roboto:wght@300;400&family=Arimo:wght@700&display=swap">
<style>
:root{
  --bar-grey:#e6e6e6;
  --page-grey:#ececec;
  --white:#ffffff;
  --ink:#222222;
  --body:#444444;
  --muted:#888888;
  --link:#2b6cb0;
  --brand:#3aa88c;
  --brand-line:#555555;
  --teal:#1fa39a;
  --green:#3db077;
  --lime:#5bbf4a;
  --lawn:#9ccc78;
  --lawn-light:#cfe6bd;
  --wood:#6e5540;
  --wall:#f2f2f0;
  --stripe-a:#1e73be;
  --stripe-b:#19b5c9;
  --stripe-c:#2fcf7a;
  --stripe-d:#5ed13b;
  --footer:#333333;
  --footer-text:#d6d6d6;
  --footer-rule:#4a4a4a;
  --map-tone:#e3e0d8;
}
*{box-sizing:border-box;margin:0;padding:0}
html,body{width:826px;height:1200px;overflow:hidden;background:var(--white)}
body{position:relative;font-family:"PT Sans",Arial,sans-serif;color:var(--body)}
a{color:var(--link);text-decoration:none}

.top-bar{position:absolute;left:0;top:0;width:826px;height:52px;background:var(--bar-grey)}
.top-bar .site-title{position:absolute;left:208px;top:16px;font-weight:700;font-size:15px;letter-spacing:.5px;color:var(--ink)}
.top-bar .icon-btn{position:absolute;top:14px;width:25px;height:25px;border:1px solid #777;border-radius:50%}
.top-bar .search{left:528px}
.top-bar .menu{left:560px}
.top-bar .menu-label{position:absolute;left:590px;top:21px;font-size:8px;font-weight:700;color:var(--ink);letter-spacing:.3px}
.top-bar svg{position:absolute;left:6px;top:6px}

.brand-band{position:absolute;left:0;top:52px;width:826px;height:105px;background:var(--white)}
.brand-name{position:absolute;left:34px;top:22px;font-family:"Roboto",sans-serif;font-weight:300;font-size:54px;letter-spacing:2px;color:var(--brand);line-height:1}
.brand-rule{position:absolute;left:181px;top:18px;width:2px;height:62px;background:var(--brand-line)}
.brand-tagline{position:absolute;left:190px;top:27px;font-family:"Roboto",sans-serif;font-weight:300;font-size:19px;line-height:21px;color:#555}

.colour-stripe{position:absolute;left:0;top:157px;width:826px;height:7px;background:linear-gradient(90deg,var(--stripe-a) 0%,var(--stripe-b) 35%,var(--stripe-c) 70%,var(--stripe-d) 100%)}

.feature-area{position:absolute;left:0;top:164px;width:826px;height:646px;background:var(--page-grey)}
.lawn{position:absolute;left:0;top:0;width:826px;height:420px;
  background:linear-gradient(180deg,var(--lawn) 0%,var(--lawn-light) 62%,var(--page-grey) 100%)}
.plan-visual{position:absolute;left:190px;top:22px;width:590px;height:340px;border-radius:14px;
  background:linear-gradient(160deg,var(--wall) 0%,#d9cfc3 22%,#8c7058 48%,var(--wood) 66%,#d8d3cc 86%,var(--wall) 100%);
  box-shadow:0 10px 24px rgba(0,0,0,.12)}
.hero-copy{position:absolute;left:76px;top:73px;width:88px;font-family:"Arimo",Arial,sans-serif;font-weight:700;font-size:11px;line-height:14.7px;color:#3d4a3a;text-align:right}

.service{position:absolute;top:414px;width:160px}
.service .badge{position:relative;height:104px}
.service .photo{position:absolute;left:0;top:0;width:100px;height:100px;border-radius:50%;background:linear-gradient(160deg,#b9d1e6 0%,#8a8c88 55%,#4f5550 100%)}
.service .disc{position:absolute;left:58px;top:12px;width:84px;height:84px;border-radius:50%;color:var(--white);font-size:9.5px;line-height:11px;text-align:center;display:flex;align-items:center;justify-content:center}
.service h3{margin-top:14px;font-size:7.5px;font-weight:700;color:var(--ink);letter-spacing:.2px}
.service p{margin-top:9px;font-size:7.4px;line-height:11.2px;color:var(--body)}
.service .more{display:inline-block;margin-top:10px;font-size:7.5px;font-weight:700;color:var(--link);border-bottom:1px solid var(--link)}
.col-a{left:170px}.col-b{left:341px}.col-c{left:511px}
.disc-teal{background:var(--teal)}.disc-green{background:var(--green)}.disc-lime{background:var(--lime)}

.widgets{position:absolute;left:0;top:810px;width:826px;height:145px;background:var(--white)}
.widget{position:absolute;top:14px;width:150px}
.widget h4{font-size:7.5px;font-weight:700;color:var(--ink);letter-spacing:.2px}
.widget p{margin-top:14px;font-size:7.4px;line-height:11px}
.widget ul{margin-top:6px;padding-left:8px;font-size:7.4px;line-height:10.5px}
.widget li a{border-bottom:1px solid #cfd9e6}
.news-item{margin-top:10px;font-size:7.4px;line-height:10px;padding-bottom:5px;border-bottom:1px solid #eee}
.news-item:first-of-type{margin-top:14px}
.news-item .date{display:block;font-size:6px;color:var(--muted)}
.w-a{left:170px}.w-b{left:338px}.w-c{left:505px;width:145px}

.site-footer{position:absolute;left:0;top:955px;width:826px;height:196px;background:var(--footer);color:var(--footer-text)}
.site-footer h4{font-size:7.5px;font-weight:700;color:var(--white);letter-spacing:.2px}
.f-col{position:absolute;top:21px;width:150px}
.f-a{left:170px}.f-b{left:338px}.f-c{left:505px;width:145px}
.map-area{margin-top:12px;width:143px;height:94px;background:var(--map-tone)}
.address{margin-top:3px;font-size:7.4px;line-height:10.5px;color:var(--white)}
.address span{border-bottom:1px solid #888}
.f-b p{margin-top:12px;font-size:7.4px;line-height:11px}
.nav-list{list-style:none;margin-top:8px}
.nav-list li{font-size:7px;font-weight:700;color:var(--white);padding:6px 0;border-bottom:1px solid var(--footer-rule)}

.base-bar{position:absolute;left:0;top:1151px;width:826px;height:49px;background:var(--white)}
.base-bar .credit{position:absolute;left:208px;top:12px;font-size:6.6px;line-height:10px;color:#555}
.social{position:absolute;left:565px;top:14px;display:flex;gap:5px}
.social span{width:7px;height:7px;background:#444;border-radius:1px}
</style>
</head>
<body>

<header class="top-bar">
  <div class="site-title">MAVO</div>
  <div class="icon-btn search"><svg width="13" height="13" viewBox="0 0 13 13"><circle cx="6" cy="6" r="2.2" fill="none" stroke="#333" stroke-width="1.2"/><line x1="7.6" y1="7.6" x2="9.5" y2="9.5" stroke="#333" stroke-width="1.3"/></svg></div>
  <div class="icon-btn menu"><svg width="13" height="13" viewBox="0 0 13 13"><g stroke="#333" stroke-width="1.2"><line x1="3" y1="4" x2="10" y2="4"/><line x1="3" y1="6.5" x2="10" y2="6.5"/><line x1="3" y1="9" x2="10" y2="9"/></g></svg></div>
  <div class="menu-label">MENU</div>
</header>

<section class="brand-band">
  <div class="brand-name">KRLM</div>
  <div class="brand-rule"></div>
  <div class="brand-tagline">Keystone Residential<br>Land Metrics</div>
</section>

<div class="colour-stripe"></div>

<main class="feature-area">
  <div class="lawn"></div>
  <div class="plan-visual" role="img" aria-label="Cut-away 3D floor plan of a furnished apartment set on a lawn"></div>
  <p class="hero-copy">Proin cursus quis mauris id sollicitu&shy;din. Mauris et nulla eget dolor dictum posuere eget et lacus. Aenean con&shy;vallis felis sed ul&shy;tricies semper. Inte&shy;ger finibus egestas nisi, a tempus elit lacinia eget. Morbi tristique lacinia sagittis. Nullam ut enim in odio ali&shy;quam ultrices</p>

  <article class="service col-a">
    <div class="badge">
      <div class="photo" role="img" aria-label="Photo of a modern apartment block"></div>
      <div class="disc disc-teal">Property<br>Report<br>Page A</div>
    </div>
    <h3>GRID PAGE</h3>
    <p>This page template displays all child pages in a grid format. This format is perfect for your case studies or services page.</p>
    <a class="more" href="#">READ MORE</a>
  </article>

  <article class="service col-b">
    <div class="badge">
      <div class="photo" role="img" aria-label="Photo of a white townhouse development"></div>
      <div class="disc disc-green">Property<br>Report<br>Page B</div>
    </div>
    <h3>FULL WIDTH PAGE</h3>
    <p>This is a full width page template. It's great for embedding a map, a large video or a contact form.</p>
    <a class="more" href="#">READ MORE</a>
  </article>

  <article class="service col-c">
    <div class="badge">
      <div class="photo" role="img" aria-label="Photo of a two-storey residential building"></div>
      <div class="disc disc-lime">Property<br>Report<br>Page C</div>
    </div>
    <h3>ALTERNATE SIDEBAR PAGE</h3>
    <p>In the theme options you can choose whether you want your sidebar on the right or on the left. Depending on which option you select, the sidebar will appear on the opposite side.</p>
    <a class="more" href="#">READ MORE</a>
  </article>
</main>

<section class="widgets">
  <div class="widget w-a">
    <h4>CUSTOM PAGE TEMPLATES</h4>
    <p>Mavo has four custom page templates that are great for business and corporate websites:</p>
    <ul>
      <li><a href="#">Front Page Template</a></li>
      <li><a href="#">Full Width Page Template</a></li>
      <li><a href="#">Grid Page Template</a></li>
      <li><a href="#">Alternate Sidebar Page Template</a></li>
    </ul>
  </div>
  <div class="widget w-b">
    <h4>SOCIAL MEDIA INTEGRATION</h4>
    <p>Mavo allows you display links to your social media profiles, like Chatter and Friendbook, as icons using a <a href="#">custom menu</a>.</p>
  </div>
  <div class="widget w-c">
    <h4>RECENT NEWS</h4>
    <div class="news-item"><a href="#">We have moved!</a><span class="date">July 30, 2014</span></div>
    <div class="news-item"><a href="#">A new model of headphones</a><span class="date">July 22, 2014</span></div>
    <div class="news-item"><a href="#">Food inspiration</a><span class="date">July 21, 2014</span></div>
  </div>
</section>

<footer class="site-footer">
  <div class="f-col f-a">
    <h4>OUR LOCATION</h4>
    <div class="map-area" role="img" aria-label="Street map showing the office location"></div>
    <p class="address"><span>48 Larkfield Road,</span><br><span>Millbrook CA 90210</span><br>1-404-555-0188</p>
  </div>
  <div class="f-col f-b">
    <h4>ABOUT US</h4>
    <p>Mavo is a fully responsive theme that helps you to create a strong–yet beautiful–online presence for your business. Mavo's layout adjusts itself depending on the device you are using. This means your site will look good not only on laptop browsers, but also on devices with smaller screens, such as the Tabla and Fonix.</p>
  </div>
  <div class="f-col f-c">
    <h4>NAVIGATION</h4>
    <ul class="nav-list">
      <li>HOME</li>
      <li>BLOG</li>
      <li>ABOUT US</li>
      <li>CONTACT US</li>
    </ul>
  </div>
</footer>

<div class="base-bar">
  <p class="credit">Create a free website or blog at SitePress.com. | The Mavo<br>Theme by SitePress.com.</p>
  <div class="social" aria-label="Social profile links"><span></span><span></span><span></span><span></span></div>
</div>

</body>
</html>
```